Stonebrace Business Card Design

The Stonebrace Co is an aggregate (crushing) equipment dealer serving Western Canadian provinces. Stonebrace is a distributor of aggregate equipment for different manufacturers.

We are looking to change and update the existing business card which has been used since the existence of the company. A copy of existing card has been attached for reference. The Stonebrace Co logo we want to remain the same and we want the green color to remain the same.

We are wanting something new with a different look. A refreshing card to show a new modern and updated look. No longer wanting to have the manufacturers on the back of the card but something more like our logo on the back of the card with a statement like "Crushing Solutions"

ideas could be:
- card can be different colors on front and back
- front or reverse of the card could possibly be the green color with the logo in black

Target Market(s)

Owners of Aggregate/Crushing companies

Contact Information for Business Card

see above

Requirements
Must have
• - logo to remain same along with same font within logo
• - green color to remain same
Nice to have
• as noted above under project description
Should not have

```html
<!DOCTYPE html>
<html lang="en">
<head>
<meta charset="utf-8">
<title>Stonebrace Business Card</title>
<link href="https://fonts.googleapis.com/css2?family=Arimo:wght@400;700&display=swap" rel="stylesheet">
<style>
  :root {
    --brand-green: #8a8c0a;
    --card-white: #ffffff;
    --card-grey: #eeeeee;
    --ink: #1e1e1e;
    --ink-soft: #3a3a3a;
    --backdrop: #e4e2df;
  }
  html, body {
    margin: 0;
    padding: 0;
    width: 1200px;
    height: 900px;
    overflow: hidden;
    background: var(--backdrop);
    font-family: "Arimo", Arial, sans-serif;
  }
  .stage {
    position: relative;
    width: 1200px;
    height: 900px;
  }
  .card {
    position: absolute;
    box-shadow: 0 6px 18px rgba(0,0,0,0.18);
    overflow: hidden;
  }
  /* Front */
  .card-front {
    left: 78px;
    top: 35px;
    width: 587px;
    height: 363px;
    background: var(--card-white);
  }
  .card-front .green-field {
    position: absolute;
    inset: 0;
  }
  .contact-block {
    position: absolute;
    right: 38px;
    top: 0;
    text-align: right;
    color: var(--card-white);
  }
  .person-name {
    margin: 60px 0 0;
    font-size: 21px;
    font-weight: 400;
    letter-spacing: 0.5px;
  }
  .contact-list {
    list-style: none;
    margin: 58px 0 0;
    padding: 0;
    font-size: 16px;
    line-height: 21px;
  }
  .contact-list li {
    display: flex;
    justify-content: flex-end;
    align-items: center;
    gap: 3px;
  }
  .contact-icon {
    width: 12px;
    height: 12px;
    fill: var(--card-white);
    flex: none;
  }
  .address {
    margin: 22px 0 0;
    font-size: 16px;
    line-height: 22px;
    font-style: normal;
  }
  /* Back */
  .card-back {
    left: 388px;
    top: 505px;
    width: 567px;
    height: 352px;
    background: var(--card-grey);
  }
  .company-name {
    position: absolute;
    left: 0;
    right: 0;
    top: 196px;
    display: flex;
    justify-content: center;
    align-items: center;
    gap: 12px;
    margin: 0;
    font-size: 23px;
    font-weight: 700;
    color: var(--ink);
    letter-spacing: 0.3px;
  }
  .company-dot {
    width: 16px;
    height: 16px;
    border-radius: 50%;
    background: var(--brand-green);
  }
  .tagline {
    position: absolute;
    left: 40px;
    right: 40px;
    top: 266px;
    display: flex;
    align-items: center;
    gap: 4px;
    margin: 0;
    font-size: 15px;
    font-weight: 700;
    color: var(--ink-soft);
    letter-spacing: 0.3px;
  }
  .tagline::before, .tagline::after {
    content: "";
    flex: 1;
    height: 1px;
    background: var(--brand-green);
  }
</style>
</head>
<body>
<main class="stage">
  <section class="card card-front" aria-label="Business card front">
    <svg class="green-field" width="587" height="363" viewBox="0 0 587 363" aria-hidden="true">
      <path d="M222 0 H587 V363 H95 C110 300 150 250 170 190 C190 120 180 60 222 0 Z" fill="var(--brand-green)"/>
    </svg>
    <div class="contact-block">
      <h1 class="person-name">DALE MORVIK</h1>
      <ul class="contact-list">
        <li>780.555.0142(Direct)<svg class="contact-icon" viewBox="0 0 12 12"><path d="M1 4c0-2 2-3 5-3s5 1 5 3v1H8.5V4h-5v1H1zM3 6h6l2 2v3H1V8z"/></svg></li>
        <li>780.555.0178<svg class="contact-icon" viewBox="0 0 12 12"><path d="M1 4c0-2 2-3 5-3s5 1 5 3v1H8.5V4h-5v1H1zM3 6h6l2 2v3H1V8z"/></svg></li>
        <li>780.555.0196<svg class="contact-icon" viewBox="0 0 12 12"><path d="M1 4h10v7H1zM3 1h6v3H3z"/><rect x="3" y="6" width="6" height="1" fill="#8a8c0a"/><rect x="3" y="8" width="6" height="1" fill="#8a8c0a"/></svg></li>
        <li>dale@stoneb.com<svg class="contact-icon" viewBox="0 0 12 12"><path d="M0 2h12v8H0z"/><path d="M0 2l6 4 6-4" fill="none" stroke="#8a8c0a" stroke-width="1"/></svg></li>
        <li>www.stonebrace.ca<svg class="contact-icon" viewBox="0 0 12 12"><circle cx="6" cy="6" r="5.5"/><path d="M0.5 6h11M6 0.5c-3 3-3 8 0 11M6 0.5c3 3 3 8 0 11" fill="none" stroke="#8a8c0a" stroke-width="0.8"/></svg></li>
      </ul>
      <address class="address">2218-52B Avenue<br>Nisku, Alberta T9E 4R2</address>
    </div>
  </section>

  <section class="card card-back" aria-label="Business card back">
    <p class="company-name"><span class="company-dot" aria-hidden="true"></span>THE STONEBRACE CO.</p>
    <p class="tagline">CRUSHING SOLUTIONS</p>
  </section>
</main>
</body>
</html>
```